Business Card & Letterhead Design

We a financial advice company based in Australia. We provide advice to wealthy farmers.

We are changing our business name FROM Brightvale Financial TO Tallowmere Wealth and we need a new letterhead and double sided business card design

Attached is designs from our previous branding (Brightvale Financial) as it includes all the details we require on the new Tallowmere Wealth business cards and letterhead.

Need extra days to review

```html
<!DOCTYPE html>
<html lang="en">
<head>
<meta charset="utf-8">
<title>Tallowmere Wealth – Business Card</title>
<link rel="stylesheet" href="https://fonts.googleapis.com/css2?family=Montserrat:wght@400;500;700&display=swap">
<style>
  :root {
    --backdrop: #2b2522;
    --card: #2e2f31;
    --card-edge: #252628;
    --ink: #f2f2f2;
    --ink-soft: #cfcfcf;
    --emboss: #1f2022;
    --emboss-line: #4a4b4e;
  }
  * { box-sizing: border-box; margin: 0; padding: 0; }
  html, body { width: 1200px; height: 800px; overflow: hidden; }
  body {
    background: var(--backdrop);
    font-family: "Montserrat", sans-serif;
    color: var(--ink);
    position: relative;
  }
  .card {
    position: absolute;
    top: 240px;
    width: 560px;
    height: 320px;
    background: var(--card);
    border: 1px solid var(--card-edge);
    box-shadow: 0 14px 30px rgba(0,0,0,.45);
    overflow: hidden;
  }
  .card--front { left: 20px; }
  .card--back { left: 620px; }

  /* Front */
  .front-brand {
    position: absolute; top: 36px; left: 0; width: 100%;
    display: flex; flex-direction: column; align-items: center;
  }
  .brand-circle {
    width: 58px; height: 58px; border-radius: 50%;
    border: 2px solid var(--emboss-line); background: var(--emboss);
  }
  .brand-name {
    margin-top: 12px;
    font-size: 24px; font-weight: 500; letter-spacing: 3px;
    text-transform: uppercase; color: var(--emboss-line);
  }
  .front-services {
    position: absolute; top: 160px; width: 100%;
    text-align: center; font-size: 13px; line-height: 1.35; color: var(--ink);
  }
  .front-licence {
    position: absolute; top: 248px; width: 100%;
    text-align: center; font-size: 13px; line-height: 1.35; color: var(--ink);
  }

  /* Back */
  .back-mark {
    position: absolute; left: -70px; top: 10px;
    width: 300px; height: 300px; border-radius: 50%;
    border: 3px solid var(--emboss-line);
    background: var(--emboss);
    display: flex; align-items: center; justify-content: center;
  }
  .back-mark-name {
    font-size: 20px; font-weight: 500; letter-spacing: 2px;
    text-transform: uppercase; color: var(--emboss-line);
    padding-left: 60px; text-align: center; line-height: 1.3;
  }
  .back-details {
    position: absolute; left: 262px; top: 30px; right: 18px;
    font-size: 12px; line-height: 1.4;
  }
  .tagline { font-weight: 700; text-align: right; margin-bottom: 8px; }
  .person-name { font-size: 17px; font-weight: 700; }
  .person-quals { font-size: 11px; font-weight: 400; }
  .person-role { color: var(--ink-soft); }
  .contact-list { list-style: none; margin-top: 2px; }
  .contact-list li { display: flex; align-items: center; gap: 6px; }
  .contact-list svg { width: 11px; height: 11px; fill: var(--ink); flex: none; }
  .address { margin-top: 8px; }
  .motto { margin-top: 12px; font-size: 13px; letter-spacing: .5px; }
</style>
</head>
<body>

<section class="card card--front" aria-label="Business card front">
  <div class="front-brand">
    <div class="brand-circle"></div>
    <div class="brand-name">Tallowmere Wealth</div>
  </div>
  <p class="front-services">
    Personal &amp; Business Insurance Solutions<br>
    Business Estate Planning<br>
    Succession Planning
  </p>
  <p class="front-licence">
    Northgate Financial Planning Limited<br>
    Australian Financial Services Licensee License Number 481902
  </p>
</section>

<section class="card card--back" aria-label="Business card back">
  <div class="back-mark">
    <span class="back-mark-name">Tallowmere<br>Wealth</span>
  </div>
  <div class="back-details">
    <p class="tagline">‘Financial peace of mind’</p>
    <p class="person-name">Sam Hartley <span class="person-quals">B.Ag.Ec. Dip F.P. CFP®</span></p>
    <p class="person-role">Managing Director<br>Authorised Representative</p>
    <ul class="contact-list">
      <li><svg viewBox="0 0 24 24"><path d="M6.6 10.8a15.1 15.1 0 0 0 6.6 6.6l2.2-2.2a1 1 0 0 1 1-.25 11.4 11.4 0 0 0 3.6.57 1 1 0 0 1 1 1V20a1 1 0 0 1-1 1A17 17 0 0 1 3 4a1 1 0 0 1 1-1h3.5a1 1 0 0 1 1 1c0 1.25.2 2.45.57 3.57a1 1 0 0 1-.25 1z"/></svg>(07) 3155 2048</li>
      <li><svg viewBox="0 0 24 24"><path d="M6 3h10v5H6zM4 9h16v11H4zm3 3v2h3v-2zm5 0v2h3v-2zm-5 4v2h3v-2zm5 0v2h3v-2z"/></svg>(07) 3155 2049</li>
      <li><svg viewBox="0 0 24 24"><path d="M7 1h10a2 2 0 0 1 2 2v18a2 2 0 0 1-2 2H7a2 2 0 0 1-2-2V3a2 2 0 0 1 2-2zm0 3v15h10V4z"/></svg>0412 660 385</li>
      <li><svg viewBox="0 0 24 24"><path d="M2 5h20v14H2zm2 2v.5l8 5 8-5V7z"/></svg>sam@brightvalefinancial.com.au</li>
      <li><svg viewBox="0 0 24 24"><circle cx="12" cy="12" r="10"/></svg>www.brightvalefinancial.com.au</li>
    </ul>
    <p class="address">
      Suite 4C, 18 Marlow St<br>
      Riverside QLD 4100<br>
      PO Box 5120, Eastwood QLD 4100
    </p>
    <p class="motto">A referral built business</p>
  </div>
</section>

</body>
</html>
```